Email Marketing Campaign- need POP ART Design

We're looking for a design to embed into our next email marketing campaign. The campaign will target small & medium businesses and the graphic will use POP ART. I included a pretty clear concept of the graphic to make this project SUPER EASY to complete!

Target Market(s)

Small and medium sized businesses

Industry/Entity Type

Tech

Requirements
Must have
• POP ART is a must! I added some images for inspiration.
Nice to have
• The graphic should be colorful and ANIMATED, just like POP ART!
Should not have
• Dry or boring colors.

```html
<!DOCTYPE html>
<html lang="en">
<head>
<meta charset="utf-8">
<title>Make your website pop – $99 per month</title>
<link rel="stylesheet" href="https://fonts.googleapis.com/css2?family=Archivo+Black&display=swap">
<style>
  :root {
    --paper: #ffffff;
    --ink: #161616;
    --purple: #8f33ea;
    --purple-light: #a34cf0;
    --blue: #1a86d6;
    --blue-light: #45aef0;
    --blue-deep: #0b5fc4;
    --skin: #f3dbb3;
    --hair: #1783cf;
    --sun: #f7d43a;
    --gold: #ffe600;
    --orange: #f5a300;
    --blast: #f4561c;
  }
  html, body {
    margin: 0;
    padding: 0;
    width: 1200px;
    height: 936px;
    overflow: hidden;
    background: var(--paper);
  }
  .promo {
    display: block;
    width: 1200px;
    height: 936px;
  }
  .headline, .feature-list, .price-line {
    font-family: "Archivo Black", "Arial Black", sans-serif;
  }
  .bubble-text { fill: var(--ink); font-size: 35px; }
  .feature-list text {
    fill: var(--paper);
    stroke: var(--ink);
    stroke-width: 2.5px;
    paint-order: stroke;
    font-size: 46px;
  }
  .feature-shadow text { fill: var(--ink); stroke: var(--ink); }
  .price-line {
    fill: url(#priceGold);
    stroke: var(--ink);
    stroke-width: 3px;
    paint-order: stroke;
  }
  .price-small { font-size: 32px; }
  .price-big { font-size: 100px; stroke-width: 6px; }
</style>
</head>
<body>
<svg class="promo" viewBox="0 0 1200 936" xmlns="http://www.w3.org/2000/svg">
  <defs>
    <radialGradient id="laptopTones" cx="0.62" cy="0.5" r="0.75">
      <stop offset="0" stop-color="var(--gold)"/>
      <stop offset="0.12" stop-color="var(--blast)"/>
      <stop offset="0.26" stop-color="var(--blue-light)"/>
      <stop offset="0.6" stop-color="var(--blue)"/>
      <stop offset="1" stop-color="var(--blue-deep)"/>
    </radialGradient>
    <linearGradient id="portraitTones" x1="0" y1="0" x2="1" y2="0">
      <stop offset="0" stop-color="var(--skin)"/>
      <stop offset="0.62" stop-color="var(--skin)"/>
      <stop offset="0.78" stop-color="var(--hair)"/>
      <stop offset="1" stop-color="var(--sun)"/>
    </linearGradient>
    <radialGradient id="purpleTones" cx="0.4" cy="0.7" r="0.8">
      <stop offset="0" stop-color="var(--purple)"/>
      <stop offset="1" stop-color="var(--purple-light)"/>
    </radialGradient>
    <linearGradient id="priceGold" x1="0" y1="0" x2="0" y2="1">
      <stop offset="0.35" stop-color="var(--gold)"/>
      <stop offset="1" stop-color="var(--orange)"/>
    </linearGradient>
  </defs>

  <!-- comic frame with purple base panel -->
  <rect class="frame" x="67" y="59" width="1066" height="828" fill="url(#purpleTones)" stroke="var(--ink)" stroke-width="4"/>

  <!-- top right panel: laptop with POP burst -->
  <path class="panel-laptop" role="img" aria-label="Laptop with a POP! comic explosion on a blue radiating halftone background"
        d="M520,59 H1133 V306 L640,386 L520,330 Z"
        fill="url(#laptopTones)" stroke="var(--paper)" stroke-width="10"/>
  <path d="M1133,312 L644,392" stroke="var(--ink)" stroke-width="4" fill="none"/>

  <!-- top left panel: whispering woman portrait -->
  <path class="panel-portrait" role="img" aria-label="Pop art woman with blue hair whispering behind her hand"
        d="M67,59 H550 Q595,190 552,306 Q430,500 235,502 Q140,502 67,458 Z"
        fill="url(#portraitTones)" stroke="var(--paper)" stroke-width="10"/>
  <path d="M67,466 Q140,508 235,508 Q430,506 556,312" stroke="var(--ink)" stroke-width="4" fill="none"/>
  <path d="M556,59 Q602,190 558,306" stroke="var(--ink)" stroke-width="3" fill="none"/>
  <rect x="67" y="59" width="1066" height="828" fill="none" stroke="var(--ink)" stroke-width="4"/>

  <!-- speech bubble -->
  <g class="speech-bubble">
    <path d="M385,296 L445,350 A135,107 0 1 0 500,318 Z" fill="var(--paper)" stroke="var(--ink)" stroke-width="6" stroke-linejoin="round"/>
    <text class="headline bubble-text" x="445" y="406" textLength="218" lengthAdjust="spacingAndGlyphs">Make your</text>
    <text class="headline bubble-text" x="445" y="443" textLength="218" lengthAdjust="spacingAndGlyphs">website ...</text>
  </g>

  <!-- price starburst -->
  <g class="price-burst">
    <polygon points="776,447 793,495 875,443 892,495 974,462 963,515 1054,501 1018,545 1109,551 1040,583 1123,611 1046,633 1095,666 1024,658 1038,707 980,688 947,735 908,688 856,738 826,688 754,718 765,666 677,683 716,633 622,628 688,600 606,573 688,556 633,515 716,506"
             fill="var(--paper)" stroke="var(--ink)" stroke-width="6" stroke-linejoin="miter"/>
    <text class="price-line price-small" x="773" y="532" textLength="190" lengthAdjust="spacingAndGlyphs" transform="rotate(3 868 522)">FOR ONLY</text>
    <text class="price-line price-big" x="771" y="620" textLength="172" lengthAdjust="spacingAndGlyphs">$99</text>
    <text class="price-line price-small" x="746" y="662" textLength="223" lengthAdjust="spacingAndGlyphs" transform="rotate(3 858 652)">PER MONTH</text>
  </g>

  <!-- feature list -->
  <g class="feature-list feature-shadow" transform="translate(-4,4)">
    <text x="103" y="578" textLength="448" lengthAdjust="spacingAndGlyphs">Get 24x7 support</text>
    <text x="103" y="636" textLength="310" lengthAdjust="spacingAndGlyphs">Site hosting</text>
    <text x="103" y="694" textLength="222" lengthAdjust="spacingAndGlyphs">Backups</text>
    <text x="103" y="750" textLength="380" lengthAdjust="spacingAndGlyphs">Design tweaks</text>
    <text x="103" y="806" textLength="689" lengthAdjust="spacingAndGlyphs">Unlimited content updates</text>
    <text x="103" y="862" textLength="296" lengthAdjust="spacingAndGlyphs">AND MORE!</text>
  </g>
  <g class="feature-list">
    <text x="103" y="578" textLength="448" lengthAdjust="spacingAndGlyphs">Get 24x7 support</text>
    <text x="103" y="636" textLength="310" lengthAdjust="spacingAndGlyphs">Site hosting</text>
    <text x="103" y="694" textLength="222" lengthAdjust="spacingAndGlyphs">Backups</text>
    <text x="103" y="750" textLength="380" lengthAdjust="spacingAndGlyphs">Design tweaks</text>
    <text x="103" y="806" textLength="689" lengthAdjust="spacingAndGlyphs">Unlimited content updates</text>
    <text x="103" y="862" textLength="296" lengthAdjust="spacingAndGlyphs">AND MORE!</text>
  </g>
</svg>
</body>
</html>
```